Sleep/Snoring Business - Requires Website - Australia

We are seeking a simple to maintain website for our sleep business. The health care business provides diagnostic and treatment solutions for snoring, sleep disorders and other respiratory problems.

Ideally, colours to match the company logo (attached).

The page must be built using WORDPRESS.

Ideally site will have a home page outlining the business, with 5 sub pages - being "Diagnosis" "Treatment Options", "Prodcuts", "About Us", "Contact Us"

The site home page should include a large picture on the home page.

The "Treatment Options" and "Diagnosis" pages must include:
Allow for a few pictures with assocaited text, plus space for some embeded youtube videos.

"Prodcuts" page should have the ability to show 3-4 products across the page with text below.. that can include external URL to products

The "About Us" page must include:
1. a Map (google map) to identify the various locations. There are 6 in total.
2. A Section to describe our doctors/staff - allow for a picture and some text

The "Contact Us" page must include:
email form
telephone details

The overall design should have a clean and medical/safe feeling

Target Market(s)

People who snore and those with sleeping and respiratory disorders

Industry/Entity Type

Health Care

Coding

Coded - Design and coding required

Number of Pages Required

5+ page

Colors

Designer to choose colors to be used in the design.

Requirements
Must have
• The page must be built using WORDPRESS.
• Ideally site will have a home page outlining the business, with 5 sub pages - being "Diagnosis" "Treatment Options", "Prodcuts", "About Us", "Contact Us"
• The site home page should include a large picture on the home page.
• The "Treatment Options" and "Diagnosis" pages must include:
• Allow for a few pictures with assocaited text, plus space for some embeded youtube videos.
• "Prodcuts" page should have the ability to show 3-4 products across the page with text below.. that can include external URL to products
• The "About Us" page must include:
• 1. a Map (google map) to identify the various locations. There are 6 in total.
• 2. A Section to describe our doctors/staff - allow for a picture and some text
• The "Contact Us" page must include:
• email form
• telephone details
• Pictures must be licenced or free to use
Nice to have
• Home page pictures showing people sleeping well, snoring or fresh air (landscape) type transition pictures (at least 3).
Should not have
• Not to look cheap
• This is a high end healthcare business, so must look that way

```html
<!DOCTYPE html>
<html lang="en">
<head>
<meta charset="utf-8">
<title>Restwell – Sleep &amp; Respiratory Care</title>
<link rel="stylesheet" href="https://fonts.googleapis.com/css2?family=Roboto:wght@400;500&family=Open+Sans:wght@400;600&display=swap">
<style>
:root{
  --navy:#0b4579;
  --navy-dark:#083863;
  --ink:#222;
  --text:#555;
  --muted:#777;
  --card:#f2f3f5;
  --line:#dcdcdc;
  --footer:#222222;
  --footer-text:#c9c9c9;
  --red:#c8362b;
  --white:#fff;
}
*{margin:0;padding:0;box-sizing:border-box}
html,body{width:1200px;height:3169px;overflow:hidden;background:var(--white)}
body{position:relative;font-family:"Open Sans",Arial,sans-serif;color:var(--text)}
.abs{position:absolute}
.heading{font-family:"Roboto",Arial,sans-serif;font-weight:500;color:var(--navy);text-align:center;width:1200px;left:0}
.rule{position:absolute;left:543px;width:114px;height:4px;background:var(--navy)}

/* header */
.site-header{position:absolute;top:0;left:0;width:1200px;height:118px;background:var(--white)}
.brand{left:86px;top:28px;display:flex;align-items:center;gap:10px;font-family:"Roboto",sans-serif;font-weight:500;font-size:40px;color:var(--navy)}
.brand-dot{width:14px;height:14px;border-radius:50%;background:var(--navy)}
.contact-item{top:16px;display:flex;align-items:center;gap:12px;font-family:"Roboto",sans-serif}
.contact-item small{display:block;font-size:10px;color:var(--muted)}
.contact-item b{display:block;font-size:14px;font-weight:500;color:var(--ink)}
.btn-appointment{left:985px;top:15px;width:128px;height:37px;background:var(--navy);color:#fff;font-family:"Roboto",sans-serif;font-size:12px;display:flex;align-items:center;justify-content:center}
.main-nav{top:66px;left:461px;display:flex;font-family:"Roboto",sans-serif;font-size:15px;color:#333}
.main-nav a{display:block;padding:0 19px;height:36px;line-height:36px;color:inherit;text-decoration:none}
.main-nav a.active{background:var(--navy);color:#fff}

/* hero */
.hero{position:absolute;top:118px;left:0;width:1200px;height:526px;overflow:hidden}
.hero-photo{position:absolute;inset:0;background:radial-gradient(ellipse at 50% 55%,#f4f8fc 0%,#dbe9f6 35%,#8fbde6 75%,#5d9fd8 100%)}
.hero-wave{position:absolute;left:0;bottom:0}
.hero-title{top:237px;width:1200px;text-align:center;font-family:"Roboto",sans-serif;font-size:58px;font-weight:400;color:var(--navy)}
.hero-sub{top:330px;width:1200px;text-align:center;font-size:16px;line-height:22px;color:#333}
.btn{height:44px;display:flex;align-items:center;justify-content:center;font-family:"Roboto",sans-serif;font-size:15px;font-weight:500;color:#fff}
.btn-primary{left:473px;top:381px;width:123px;background:var(--navy)}
.btn-dark{left:604px;top:381px;width:123px;background:#111}
.slider-arrow{width:22px;height:22px;border-radius:50%;background:#111;display:flex;align-items:center;justify-content:center}

/* offer cards */
.offer-card{top:818px;width:326px;height:401px;background:var(--card);border:1px solid var(--line)}
.offer-card.featured{box-shadow:0 10px 24px rgba(0,0,0,.18);border-color:#e4e4e4}
.offer-photo{position:absolute;left:0;top:0;width:100%;height:211px}
.offer-curve{position:absolute;left:0;top:150px}
.offer-title{position:absolute;top:240px;width:100%;text-align:center;font-family:"Roboto",sans-serif;font-size:22px;color:#333}
.featured .offer-title{color:var(--navy)}
.offer-text{position:absolute;top:281px;left:28px;right:28px;text-align:center;font-size:12.5px;line-height:21px;color:var(--text)}
.offer-more{position:absolute;top:352px;width:100%;text-align:center;font-size:12.5px;color:#444}
.featured .offer-more{color:var(--navy)}

/* video band */
.video-band{position:absolute;top:1300px;left:0;width:1200px;height:509px;background:linear-gradient(90deg,#3b3b3b 0%,#4a4a4a 40%,#5b5a58 55%,#3d3d3d 100%)}
.video-title{top:155px;width:1200px;text-align:center;font-family:"Roboto",sans-serif;font-size:56px;color:#fff}
.play{left:541px;top:241px}

/* news */
.news-card{top:1980px;width:502px;height:207px;border:1px solid var(--line);background:#fff}
.news-photo{position:absolute;left:0;top:0;width:237px;height:100%}
.news-body{position:absolute;left:250px;top:14px;right:12px}
.news-body h3{font-family:"Roboto",sans-serif;font-weight:400;font-size:17px;line-height:25px;color:#222}
.news-meta{display:flex;gap:18px;font-size:11.5px;color:#555;margin:6px 0 14px;align-items:center}
.news-meta span{display:flex;align-items:center;gap:5px}
.news-body p{font-size:12.5px;line-height:21px;color:#444}
.news-more{margin-top:12px;font-size:12.5px;color:#444}

/* testimonials */
.clients{position:absolute;top:2263px;left:0;width:1200px;height:435px;background:var(--navy)}
.clients .heading{color:#fff;top:58px;font-size:44px;font-weight:400}
.clients .rule{top:126px;background:#fff;height:3px}
.quote{top:192px;width:320px}
.quote p{margin-top:12px;font-size:12px;line-height:20px;color:#e6eef6}
.person{display:flex;align-items:center;gap:18px;margin-top:28px}
.avatar{width:68px;height:68px;border-radius:50%;border:3px solid #fff}
.person b{display:block;font-family:"Roboto",sans-serif;font-weight:500;font-size:16px;color:#fff}
.person small{display:block;font-size:11px;color:#c8d6e6;margin-top:4px}
.round-arrow{width:30px;height:30px;border-radius:50%;background:#6f8aa6;display:flex;align-items:center;justify-content:center}

/* footer */
.site-footer{position:absolute;top:2698px;left:0;width:1200px;height:471px;background:var(--footer);color:var(--footer-text)}
.footer-col{top:78px}
.footer-col h4{font-family:"Roboto",sans-serif;font-weight:500;font-size:17px;color:#fff;letter-spacing:.3px}
.footer-col .underline{width:244px;height:1px;background:#555;margin-top:12px}
.info-row{display:flex;gap:22px;font-size:13px;line-height:22px;color:#ddd;position:absolute;left:0}
.newsletter p{font-size:13px;line-height:22px;color:#ccc;margin-top:26px}
.email-field{margin-top:14px;width:256px;height:42px;background:#fff;font-size:11px;color:#888;padding:0 18px;display:flex;align-items:center}
.submit{margin-top:12px;width:256px;height:41px;background:var(--navy);color:#fff;font-family:"Roboto",sans-serif;font-weight:500;font-size:16px;display:flex;align-items:center;justify-content:center}
.quick-links{list-style:none;margin-top:26px}
.quick-links li{font-size:12px;color:#ddd;height:30.5px;line-height:20px}
.quick-links li::before{content:">";margin-right:12px}
.social{top:3034px;display:flex;gap:10px}
.social span{width:30px;height:30px;border-radius:50%}
.footer-divider{position:absolute;top:396px;left:87px;width:1022px;height:1px;background:#444}
.copyright{top:428px;width:1200px;text-align:center;font-size:14px;color:#bbb}
</style>
</head>
<body>

<header class="site-header">
  <div class="abs brand"><span class="brand-dot"></span>Restwell</div>

  <div class="abs contact-item" style="left:632px">
    <svg width="26" height="26" viewBox="0 0 24 24"><path fill="#0b4579" d="M6.6 10.8c1.4 2.8 3.8 5.1 6.6 6.6l2.2-2.2c.3-.3.7-.4 1-.2 1.1.4 2.3.6 3.6.6.6 0 1 .4 1 1V20c0 .6-.4 1-1 1C10.6 21 3 13.4 3 4c0-.6.4-1 1-1h3.5c.6 0 1 .4 1 1 0 1.3.2 2.5.6 3.6.1.3 0 .7-.2 1z"/></svg>
    <div><small>TOLL FREE</small><b>0400 517 302</b></div>
  </div>
  <div class="abs contact-item" style="left:815px">
    <svg width="34" height="26" viewBox="0 0 34 26"><rect x="0" y="2" width="34" height="22" fill="#0b4579"/><path d="M1 3l16 12L33 3" stroke="#fff" stroke-width="2.5" fill="none"/></svg>
    <div><small>MAIL US</small><b>info@restwell.com</b></div>
  </div>
  <div class="abs btn-appointment">Appointment Now</div>

  <nav class="abs main-nav">
    <a class="active">HOME</a><a>DIAGNOSIS</a><a>TREATMENT OPTIONS</a><a>ABOUT US</a><a>CONTACT US</a>
  </nav>
</header>

<section class="hero">
  <div class="hero-photo" role="img" aria-label="Woman sleeping peacefully on a soft white cloud under a blue sky"></div>
  <h1 class="abs hero-title">WELCOME TO Restwell</h1>
  <p class="abs hero-sub">We provide diagnostic and treatment solutions for snoring, sleep disorders<br>and other respiratory problems.</p>
  <a class="abs btn btn-primary">READ MORE</a>
  <a class="abs btn btn-dark">CONTACT US</a>
  <div class="abs slider-arrow" style="left:31px;top:254px"><svg width="10" height="10" viewBox="0 0 10 10"><path d="M7 1L3 5l4 4" stroke="#fff" stroke-width="2" fill="none"/></svg></div>
  <div class="abs slider-arrow" style="left:1145px;top:254px"><svg width="10" height="10" viewBox="0 0 10 10"><path d="M3 1l4 4-4 4" stroke="#fff" stroke-width="2" fill="none"/></svg></div>
  <svg class="hero-wave" width="1200" height="50" viewBox="0 0 1200 50" preserveAspectRatio="none"><path d="M0 20 Q600 -20 1200 20 L1200 50 L0 50 Z" fill="#fff"/></svg>
</section>

<section class="offer">
  <h2 class="abs heading" style="top:706px;font-size:46px">WE OFFER</h2>
  <div class="rule" style="top:775px"></div>

  <article class="abs offer-card" style="left:87px">
    <div class="offer-photo" role="img" aria-label="Couple in bed, one snoring while the other covers her ears" style="background:linear-gradient(135deg,#cfc4bb,#e9e2da 55%,#b9aca2)"></div>
    <svg class="offer-curve" width="326" height="62" viewBox="0 0 326 62" preserveAspectRatio="none"><path d="M0 62 L0 50 Q163 -10 326 50 L326 62 Z" fill="#f2f3f5"/></svg>
    <h3 class="offer-title">SNORING</h3>
    <p class="offer-text">Lorem Ipsum is simply dummy text of the print-ing and typesetting industry. Lorem Ipsum has been the industry's standard...</p>
    <a class="offer-more">Read More &gt;</a>
  </article>

  <article class="abs offer-card featured" style="left:435px">
    <div class="offer-photo" role="img" aria-label="Woman in bed wearing a sleep therapy mask" style="background:linear-gradient(135deg,#dfe3e6,#f3f4f5 50%,#c5ccd3)"></div>
    <svg class="offer-curve" width="326" height="62" viewBox="0 0 326 62" preserveAspectRatio="none"><path d="M0 62 L0 50 Q163 -10 326 50 L326 62 Z" fill="#f2f3f5"/></svg>
    <h3 class="offer-title">SLEEP DISORDERS</h3>
    <p class="offer-text">Lorem Ipsum is simply dummy text of the print-ing and typesetting industry. Lorem Ipsum has been the industry's standard...</p>
    <a class="offer-more">Read More &gt;</a>
  </article>

  <article class="abs offer-card" style="left:784px">
    <div class="offer-photo" role="img" aria-label="Woman holding her chest with breathing discomfort" style="background:linear-gradient(135deg,#3f3f45,#6a5d5e 55%,#2e2e33)"></div>
    <svg class="offer-curve" width="326" height="62" viewBox="0 0 326 62" preserveAspectRatio="none"><path d="M0 62 L0 50 Q163 -10 326 50 L326 62 Z" fill="#f2f3f5"/></svg>
    <h3 class="offer-title">RESPIRATORY PROBLEMS</h3>
    <p class="offer-text">Lorem Ipsum is simply dummy text of the print-ing and typesetting industry. Lorem Ipsum has been the industry's standard...</p>
    <a class="offer-more">Read More &gt;</a>
  </article>
</section>

<section class="video-band" role="img" aria-label="Doctor holding a breathing mask, dimmed video still">
  <h2 class="abs video-title">DIAGNOSTIC TECHNIQUES</h2>
  <svg class="abs play" width="118" height="118" viewBox="0 0 118 118"><circle cx="59" cy="59" r="59" fill="#c8362b"/><path d="M46 36 L84 59 L46 82 Z" fill="#fff"/></svg>
</section>

<section class="news">
  <h2 class="abs heading" style="top:1886px;font-size:46px">LATEST NEWS</h2>
  <div class="rule" style="top:1942px"></div>

  <article class="abs news-card" style="left:87px">
    <div class="news-photo" role="img" aria-label="Woman at a table holding a cup" style="background:linear-gradient(135deg,#6e7d5a,#c9866a 55%,#d9c3a8)"></div>
    <div class="news-body">
      <h3>The standard Lorem Ipsum passage, used since</h3>
      <div class="news-meta">
        <span><svg width="12" height="12" viewBox="0 0 12 12"><rect x="1" y="2" width="10" height="9" fill="none" stroke="#555"/><path d="M1 5h10" stroke="#555"/></svg>22.06.2017</span>
        <span><svg width="13" height="11" viewBox="0 0 13 11"><path d="M1 1h11v7H5l-3 2V8H1z" fill="#555"/></svg>45</span>
      </div>
      <p>Lorem Ipsum is simply dummy text of the printing and typesetting...</p>
      <div class="news-more">Read More &gt;</div>
    </div>
  </article>

  <article class="abs news-card" style="left:608px">
    <div class="news-photo" role="img" aria-label="Older man on a sofa coughing" style="background:linear-gradient(135deg,#d8d4cc,#b9b6ae 55%,#9aa66a)"></div>
    <div class="news-body">
      <h3>The standard Lorem Ipsum passage, used since</h3>
      <div class="news-meta">
        <span><svg width="12" height="12" viewBox="0 0 12 12"><rect x="1" y="2" width="10" height="9" fill="none" stroke="#555"/><path d="M1 5h10" stroke="#555"/></svg>18.06.2017</span>
        <span><svg width="13" height="11" viewBox="0 0 13 11"><path d="M1 1h11v7H5l-3 2V8H1z" fill="#555"/></svg>85</span>
      </div>
      <p>Lorem Ipsum is simply dummy text of the printing and typesetting...</p>
      <div class="news-more">Read More &gt;</div>
    </div>
  </article>
</section>

<section class="clients">
  <h2 class="abs heading">OUR CLIENTS SAYS</h2>
  <div class="rule"></div>

  <div class="abs round-arrow" style="left:25px;top:264px"><svg width="10" height="12" viewBox="0 0 10 12"><path d="M7 1L2 6l5 5" stroke="#fff" stroke-width="2" fill="none"/></svg></div>
  <div class="abs round-arrow" style="left:1143px;top:264px"><svg width="10" height="12" viewBox="0 0 10 12"><path d="M3 1l5 5-5 5" stroke="#fff" stroke-width="2" fill="none"/></svg></div>

  <div class="abs quote" style="left:91px">
    <svg width="24" height="18" viewBox="0 0 24 18"><path d="M0 18V9Q0 2 8 0v4Q4 5 4 9h5v9zM14 18V9q0-7 8-9v4q-4 1-4 5h5v9z" fill="#fff"/></svg>
    <p>Lorem Ipsum is simply dummy text of the printing and typesetting industry. Lorem Ipsum has been the indus-try's standard dummy..</p>
    <div class="person"><div class="avatar" role="img" aria-label="Client portrait" style="background:#c89a78"></div><div><b>Marion K Hale</b><small>Vienna</small></div></div>
  </div>
  <div class="abs quote" style="left:446px">
    <svg width="24" height="18" viewBox="0 0 24 18"><path d="M0 18V9Q0 2 8 0v4Q4 5 4 9h5v9zM14 18V9q0-7 8-9v4q-4 1-4 5h5v9z" fill="#fff"/></svg>
    <p>Lorem Ipsum is simply dummy text of the printing and typesetting industry. Lorem Ipsum has been the indus-try's standard dummy..</p>
    <div class="person"><div class="avatar" role="img" aria-label="Client portrait" style="background:#b7aaa0"></div><div><b>Peter J Lowe</b><small>OFENBACH</small></div></div>
  </div>
  <div class="abs quote" style="left:799px">
    <svg width="24" height="18" viewBox="0 0 24 18"><path d="M0 18V9Q0 2 8 0v4Q4 5 4 9h5v9zM14 18V9q0-7 8-9v4q-4 1-4 5h5v9z" fill="#fff"/></svg>
    <p>Lorem Ipsum is simply dummy text of the printing and typesetting industry. Lorem Ipsum has been the indus-try's standard dummy..</p>
    <div class="person"><div class="avatar" role="img" aria-label="Client portrait" style="background:#8a6a5a"></div><div><b>Alice R Dunn</b><small>Styria</small></div></div>
  </div>
</section>

<footer class="site-footer">
  <div class="abs footer-col" style="left:87px;width:300px;height:250px">
    <h4>GET IN TOUCH</h4>
    <div class="underline"></div>
    <div class="info-row" style="top:72px">
      <svg width="10" height="14" viewBox="0 0 10 14" style="margin-top:4px"><path d="M5 0a5 5 0 0 1 5 5c0 4-5 9-5 9S0 9 0 5a5 5 0 0 1 5-5z" fill="#fff"/><circle cx="5" cy="5" r="2" fill="#222"/></svg>
      <div>Restwell, Harbour Road 14,<br>NORTHGATE, Queensland, 4013.</div>
    </div>
    <div class="info-row" style="top:128px">
      <svg width="12" height="12" viewBox="0 0 24 24" style="margin-top:5px"><path fill="#fff" d="M6.6 10.8c1.4 2.8 3.8 5.1 6.6 6.6l2.2-2.2c.3-.3.7-.4 1-.2 1.1.4 2.3.6 3.6.6.6 0 1 .4 1 1V20c0 .6-.4 1-1 1C10.6 21 3 13.4 3 4c0-.6.4-1 1-1h3.5c.6 0 1 .4 1 1 0 1.3.2 2.5.6 3.6.1.3 0 .7-.2 1z"/></svg>
      <div>0400 517 302</div>
    </div>
    <div class="info-row" style="top:170px">
      <svg width="13" height="10" viewBox="0 0 13 10" style="margin-top:6px"><rect width="13" height="10" fill="#fff"/><path d="M0 0l6.5 5L13 0" stroke="#222" fill="none"/></svg>
      <div>info@restwell.com</div>
    </div>
  </div>

  <div class="abs footer-col newsletter" style="left:473px">
    <h4>NEWSLETTER SIGN UP</h4>
    <div class="underline"></div>
    <p>Don't miss our news and updates.<br>Subscribe now!</p>
    <div class="email-field">Enter Email</div>
    <div class="submit">SUBMIT</div>
  </div>

  <div class="abs footer-col" style="left:866px">
    <h4>QUICK LINK</h4>
    <div class="underline"></div>
    <ul class="quick-links">
      <li>HOME</li><li>DIAGNOSIS</li><li>TREATMENT OPTIONS</li><li>ABOUT US</li><li>CONTACT US</li>
    </ul>
  </div>

  <div class="abs" style="left:85px;top:320px;display:flex;gap:10px">
    <span style="width:30px;height:30px;border-radius:50%;background:#3b5998"></span>
    <span style="width:30px;height:30px;border-radius:50%;background:#2aa3ef"></span>
    <span style="width:30px;height:30px;border-radius:50%;background:#d34836"></span>
    <span style="width:30px;height:30px;border-radius:50%;background:#cc2020"></span>
  </div>

  <div class="footer-divider"></div>
  <p class="abs copyright">Copyright © 2017 &nbsp;Restwell. All rights reserved</p>
</footer>

</body>
</html>
```